Heritage Hollow Business Cards

Require a business card design. <br/><br/>Needs to include logo (either round or long version) plus these details:<br/>Maya Torvell<br/>Heritage Hollow<br/>maya@kelvadtrading.com.au<br/>02 6481 7395<br/>PO Box Glenwarra NSW 2791<br/>www.heritagehollow.com.au<br/><br/>I need in an editable format so that I can create for multiple staff members. <br/><br/>

Target Market(s)

We are an online store selling renovation products to home owners are builders. Looking for a classic classy design.

Industry/Entity Type

Home And Garden

Contact Information for Business Card

Maya Torvell
Heritage Hollow
maya@kelvadtrading.com.au
02 6481 7395
PO Box Glenwarra NSW 2791
www.heritagehollow.com.au

Colors

Designer to choose colors to be used in the design.

Requirements
Must have
• Must include Logo.

```html
<!DOCTYPE html>
<html lang="en">
<head>
<meta charset="utf-8">
<title>Heritage Hollow – Business Card</title>
<link href="https://fonts.googleapis.com/css2?family=Arimo:wght@400;700&display=swap" rel="stylesheet">
<style>
  :root {
    --page-bg: #e6e4e2;
    --card-light: #f7f6f5;
    --card-dark: #272526;
    --ink-dark: #3a3839;
    --ink-light: #ffffff;
  }
  * { margin: 0; padding: 0; box-sizing: border-box; }
  html, body {
    width: 1200px;
    height: 900px;
    overflow: hidden;
    background: var(--page-bg);
    font-family: "Arimo", Arial, sans-serif;
  }
  .business-card {
    position: absolute;
    left: 110px;
    top: 150px;
    width: 980px;
    height: 600px;
    background: var(--card-light);
    overflow: hidden;
    box-shadow: 0 10px 30px rgba(0,0,0,0.18);
  }
  .dark-panel {
    position: absolute;
    inset: 0;
    width: 100%;
    height: 100%;
  }
  .brand {
    position: absolute;
    left: 44px;
    top: 160px;
    display: flex;
    align-items: center;
    gap: 18px;
  }
  .brand-mark {
    width: 64px;
    height: 64px;
    border-radius: 50%;
    background: var(--ink-dark);
  }
  .brand-name {
    font-size: 46px;
    font-weight: 400;
    color: var(--ink-dark);
    letter-spacing: 0.5px;
  }
  .contact-block {
    position: absolute;
    right: 70px;
    top: 244px;
    text-align: right;
    color: var(--ink-light);
  }
  .staff-name {
    font-size: 32px;
    font-weight: 700;
    letter-spacing: 0.5px;
    margin-bottom: 50px;
  }
  .postal-address {
    font-size: 26px;
    line-height: 36px;
    margin-bottom: 28px;
  }
  .contact-line {
    display: flex;
    justify-content: flex-end;
    align-items: center;
    gap: 12px;
    font-size: 26px;
    line-height: 38px;
  }
  .contact-icon {
    width: 28px;
    height: 28px;
    flex: none;
  }
</style>
</head>
<body>
  <div class="business-card">
    <svg class="dark-panel" viewBox="0 0 980 600" preserveAspectRatio="none" aria-hidden="true">
      <polygon fill="var(--card-dark)"
        points="882,0 980,0 980,600 120,600 130,588 210,540 206,532 300,480 380,432 376,424 470,372 560,318 556,310 650,256 740,200 736,192 820,140 870,96 866,88 900,40 876,20"/>
      <polyline fill="none" stroke="#1a1819" stroke-width="3"
        points="120,600 210,540 300,480 380,432 470,372 560,318 650,256 740,200 820,140 870,96 900,40 882,0"/>
    </svg>

    <div class="brand">
      <span class="brand-mark"></span>
      <span class="brand-name">Heritage Hollow</span>
    </div>

    <div class="contact-block">
      <div class="staff-name">MAYA TORVELL</div>
      <div class="postal-address">PO Box Glenwarra<br>NSW 2791</div>

      <div class="contact-line">
        <span>02 6481 7395</span>
        <svg class="contact-icon" viewBox="0 0 28 28" aria-hidden="true">
          <rect x="2" y="2" width="24" height="24" rx="4" fill="none" stroke="#fff" stroke-width="2"/>
          <path d="M9 7c1 0 2 2.5 2 3.2s-1.3 1.1-1 2c.7 2 2.6 3.9 4.6 4.6.9.3 1.3-1 2-1s3.2 1 3.2 2-1.5 2.4-2.8 2.2C12 19.2 8.8 16 7.9 11 7.7 9.6 8 7 9 7z" fill="#fff"/>
        </svg>
      </div>
      <div class="contact-line">
        <span>maya@kelvadtrading.com.au</span>
        <svg class="contact-icon" viewBox="0 0 28 28" aria-hidden="true">
          <rect x="2" y="6" width="24" height="16" fill="#fff"/>
          <polyline points="2,6 14,16 26,6" fill="none" stroke="var(--card-dark)" stroke-width="2"/>
        </svg>
      </div>
      <div class="contact-line">
        <span>www.heritagehollow.com.au</span>
        <svg class="contact-icon" viewBox="0 0 28 28" aria-hidden="true">
          <circle cx="14" cy="14" r="12" fill="#fff"/>
          <g fill="none" stroke="var(--card-dark)" stroke-width="1.6">
            <ellipse cx="14" cy="14" rx="5" ry="12"/>
            <line x1="14" y1="2" x2="14" y2="26"/>
            <line x1="2" y1="14" x2="26" y2="14"/>
            <path d="M4.5 8h19M4.5 20h19"/>
          </g>
        </svg>
      </div>
    </div>
  </div>
</body>
</html>
```